TernVAX Business Cards

Create business cards for our exciting new software company. We provide cloud billing systems and provisioning software for campany that need monthly SaaS and Cloud Billing

Target Market(s)

Enterprise businesses, b2b, telecom carriers, software manufactures

Industry/Entity Type

Software

```html
<!DOCTYPE html>
<html lang="en">
<head>
<meta charset="utf-8">
<title>TernVAX Business Cards</title>
<link rel="stylesheet" href="https://fonts.googleapis.com/css2?family=Questrial&display=swap">
<style>
  :root {
    --backdrop: #3b3b3d;
    --navy: #1f3552;
    --sky: #6fb8dc;
    --paper: #f1f1f1;
    --ink: #1f3552;
    --muted: #6b7686;
    --url-light: #aab7c7;
  }
  * { margin: 0; padding: 0; box-sizing: border-box; }
  html, body { width: 1200px; height: 900px; overflow: hidden; }
  body {
    background: var(--backdrop);
    font-family: "Questrial", "Century Gothic", sans-serif;
    position: relative;
  }
  .card {
    position: absolute;
    top: 300px;
    width: 525px;
    height: 300px;
    border-radius: 22px;
  }
  .card--front { left: 58px; background: var(--navy); }
  .card--back { left: 617px; background: var(--paper); }

  .block {
    position: absolute;
    right: 50px;
    text-align: right;
    white-space: nowrap;
  }
  .brand { line-height: 1; letter-spacing: 0.2px; }
  .tagline {
    text-transform: uppercase;
    font-size: 5.6px;
    letter-spacing: 0.8px;
    line-height: 8px;
  }

  /* front */
  .card--front .brand { top: 210px; font-size: 30px; color: var(--sky); }
  .card--front .tagline { top: 243px; color: #d7e2ee; }
  .card--front .url {
    top: 269px;
    font-size: 8.5px;
    letter-spacing: 5.2px;
    margin-right: -5px;
    color: var(--url-light);
  }

  /* back */
  .card--back .brand { top: 148px; font-size: 25px; color: var(--ink); }
  .card--back .tagline { top: 175px; color: var(--muted); font-size: 5px; line-height: 7px; }
  .contact { top: 204px; color: var(--ink); }
  .contact .name { font-size: 13.5px; letter-spacing: 0.9px; line-height: 15px; }
  .contact .role { font-size: 10px; letter-spacing: 1px; line-height: 12px; }
  .contact .lines { margin-top: 10px; font-size: 12px; letter-spacing: 0.8px; line-height: 12.5px; }
  .contact .label { color: var(--muted); }
  .contact .web { margin-top: 7px; font-size: 12px; letter-spacing: 1px; font-weight: bold; }
</style>
</head>
<body>
  <section class="card card--front" aria-label="Card front">
    <div class="block brand">TernVAX</div>
    <div class="block tagline">Cloud billing and<br>operational support systems</div>
    <div class="block url">WWW.TERNVAX.COM</div>
  </section>

  <section class="card card--back" aria-label="Card back">
    <div class="block brand">TernVAX</div>
    <div class="block tagline">Cloud billing and<br>operational support systems</div>
    <div class="block contact">
      <div class="name">MAREN HOLLOWAY</div>
      <div class="role">MANAGER</div>
      <div class="lines">
        <div><span class="label">P:</span> 555-014-2207 <span class="label">F:</span> 555-014-7600</div>
        <div><span class="label">E:</span> INFO@TERNVAX.COM</div>
      </div>
      <div class="web">WWW.TERNVAX.COM</div>
    </div>
  </section>
</body>
</html>
```